business card for a massage therapy practice named 'Cedar and Willow Massage Studio'

I really need a trendy, yet easy on the eyes business card to complement my logo. Ideally with some gold or rose gold foil work.

My uploaded file of the logo I have in horizontal but I have a vertical version as well. Another color that is used in the website is a blush pink here and there. I'd like to see some trendy tropical leaves in the design.

```html
<!DOCTYPE html>
<html lang="en">
<head>
<meta charset="utf-8">
<title>Cedar and Willow Massage Studio – Business Card</title>
<link rel="stylesheet" href="https://fonts.googleapis.com/css2?family=Open+Sans:wght@400;600&display=swap">
<style>
  :root {
    --page: #e4e4e6;
    --card-white: #ffffff;
    --card-dark: #45454b;
    --ink: #2b2b2b;
    --mint: #5fcfb3;
    --gold: #b49a63;
    --rule: #c9c9c9;
    --dot-blue: #3b67b3;
    --dot-red: #d9473a;
    --dot-crimson: #c8232c;
    --dot-steel: #3f7fb5;
    --skin-a: #e2b7a3;
    --skin-b: #b9b6b4;
  }
  * { box-sizing: border-box; margin: 0; padding: 0; }
  html, body { width: 1200px; height: 896px; overflow: hidden; }
  body {
    background: var(--page);
    font-family: "Open Sans", Arial, sans-serif;
    color: var(--ink);
    display: flex;
    flex-direction: column;
    align-items: center;
    justify-content: center;
    gap: 56px;
  }
  .card {
    width: 640px;
    height: 366px;
    position: relative;
    overflow: hidden;
    box-shadow: 0 6px 18px rgba(0,0,0,.18);
  }

  /* Front */
  .card--front { background: var(--card-white); }
  .contact {
    position: absolute;
    left: 44px;
    top: 70px;
  }
  .contact__name {
    color: var(--mint);
    font-size: 19px;
    letter-spacing: 1px;
    text-transform: uppercase;
  }
  .contact__role { font-size: 15px; margin-bottom: 10px; }
  .contact__line {
    display: flex;
    align-items: center;
    gap: 8px;
    font-size: 14px;
    line-height: 22px;
  }
  .contact__line svg { width: 14px; height: 14px; fill: var(--mint); }

  .brand {
    position: absolute;
    right: 48px;
    top: 80px;
    display: flex;
    align-items: center;
    gap: 14px;
  }
  .brand__dot {
    width: 44px; height: 44px;
    border-radius: 50%;
    background: var(--gold);
  }
  .brand__name {
    font-size: 22px;
    font-weight: 600;
    line-height: 1.25;
    color: var(--ink);
  }
  .card--back .brand__name { color: #ffffff; }
  .card--back .brand__dot { background: #ffffff; }

  .rule {
    position: absolute;
    left: 44px;
    right: 150px;
    top: 250px;
    border-top: 1px solid var(--rule);
  }
  .social {
    position: absolute;
    right: 44px;
    top: 240px;
    display: flex;
    gap: 8px;
  }
  .social span { width: 20px; height: 20px; border-radius: 50%; }
  .social .s1 { background: var(--dot-blue); }
  .social .s2 { background: var(--dot-red); }
  .social .s3 { background: var(--dot-crimson); }
  .social .s4 { background: var(--dot-steel); }
  .address {
    position: absolute;
    right: 44px;
    top: 276px;
    text-align: right;
    font-size: 15px;
    line-height: 22px;
  }

  /* Back */
  .card--back { background: var(--card-dark); }
  .card--back .brand { left: 50%; right: auto; top: 52px; transform: translateX(-50%); }
  .photo {
    position: absolute;
    left: 0; right: 0; bottom: 0;
    height: 170px;
    background: linear-gradient(100deg, var(--skin-b) 0%, var(--skin-b) 30%, var(--skin-a) 55%, #c99c86 100%);
  }
</style>
</head>
<body>
  <section class="card card--front">
    <div class="contact">
      <p class="contact__name">Marisol Vega</p>
      <p class="contact__role">Massage Therapist</p>
      <p class="contact__line">
        <svg viewBox="0 0 16 16" aria-hidden="true"><path d="M3 1h3l1.5 4-2 1.3a9 9 0 0 0 4.2 4.2L11 8.5l4 1.5v3a2 2 0 0 1-2 2A12 12 0 0 1 1 3a2 2 0 0 1 2-2z"/></svg>
        (555) 014-2380
      </p>
      <p class="contact__line">
        <svg viewBox="0 0 16 16" aria-hidden="true"><path d="M1 3h14v10H1z M1 3l7 6 7-6" stroke="#fff" stroke-width="1.2"/></svg>
        cedarandwillow@mail.com
      </p>
    </div>
    <div class="brand">
      <span class="brand__dot"></span>
      <p class="brand__name">Cedar and Willow<br>Massage Studio</p>
    </div>
    <div class="rule"></div>
    <div class="social" aria-hidden="true">
      <span class="s1"></span><span class="s2"></span><span class="s3"></span><span class="s4"></span>
    </div>
    <p class="address">4870 Alder Ave. suite 210<br>Riverton, CA 90000</p>
  </section>

  <section class="card card--back">
    <div class="brand">
      <span class="brand__dot"></span>
      <p class="brand__name">Cedar and Willow<br>Massage Studio</p>
    </div>
    <div class="photo" role="img" aria-label="Photo of hands giving a shoulder massage to a client in a grey sweater"></div>
  </section>
</body>
</html>
```